LHP Letterhead

I need letterhead for "maple crest holdings llc" ...

logo attached to project..

Company Info:
815 East Darrow Avenue, Suite 4B
Chicago, Illinois 60417
ofc 312-555-0148
facsimile 312-555-0192
www.maplecrestholdingsllc.example
info@maplecrestholdingsllc.example

I have multiple projects listed.. see below:

Business cards for maple crest holdings llc
letterhead "
envelopes "

Business cards for KP Exchange LLC
letterhead "
envelopes "

Industry/Entity Type

It Company

```html
<!DOCTYPE html>
<html lang="en">
<head>
<meta charset="utf-8">
<title>Maple Crest Holdings LLC — Letterhead</title>
<link href="https://fonts.googleapis.com/css2?family=Roboto+Condensed:wght@400;500&display=swap" rel="stylesheet">
<style>
  :root {
    --backdrop: #e6e7e9;
    --paper: #ffffff;
    --brand-navy: #154274;
    --brand-navy-deep: #10365f;
    --swoosh-light: #f2f2f2;
    --swoosh-mid: #c9c9cb;
    --footer-text: #ffffff;
  }
  * { margin: 0; padding: 0; box-sizing: border-box; }
  html, body {
    width: 1200px;
    height: 1000px;
    overflow: hidden;
    background: var(--backdrop);
    font-family: "Roboto Condensed", "Arial Narrow", sans-serif;
  }
  .letterhead {
    position: absolute;
    left: 294px;
    top: 85px;
    width: 601px;
    height: 845px;
    background: var(--paper);
    overflow: hidden;
  }
  .brand {
    position: absolute;
    right: 36px;
    top: 96px;
    display: flex;
    align-items: center;
    gap: 10px;
  }
  .brand-mark {
    width: 22px;
    height: 22px;
    border-radius: 50%;
    background: var(--brand-navy);
  }
  .brand-text { text-align: left; }
  .brand-name {
    display: block;
    color: var(--brand-navy);
    font-weight: 500;
    font-size: 16px;
    letter-spacing: 0.6px;
    text-transform: uppercase;
    line-height: 18px;
  }
  .brand-web {
    display: block;
    color: var(--brand-navy);
    font-weight: 500;
    font-size: 11px;
    letter-spacing: 1.3px;
    line-height: 14px;
  }
  .footer-band {
    position: absolute;
    left: 0;
    bottom: 0;
    width: 601px;
    height: 110px;
  }
  .footer-band svg { display: block; }
  .footer-contact {
    position: absolute;
    left: 0;
    right: 0;
    bottom: 12px;
    text-align: center;
    color: var(--footer-text);
    font-size: 10.5px;
    line-height: 13px;
  }
  .footer-contact .sep { padding: 0 3px; }
</style>
</head>
<body>
  <main class="letterhead">
    <header class="brand">
      <span class="brand-mark" aria-hidden="true"></span>
      <div class="brand-text">
        <span class="brand-name">Maple Crest Holdings LLC</span>
        <span class="brand-web">www.maplecrestholdingsllc.example</span>
      </div>
    </header>

    <footer class="footer-band">
      <svg width="601" height="110" viewBox="0 0 601 110" aria-hidden="true">
        <defs>
          <linearGradient id="swooshFade" x1="0" y1="0" x2="1" y2="0">
            <stop offset="0" stop-color="var(--swoosh-mid)"/>
            <stop offset="0.55" stop-color="var(--swoosh-mid)" stop-opacity="0.7"/>
            <stop offset="1" stop-color="var(--swoosh-light)"/>
          </linearGradient>
        </defs>
        <path class="swoosh" d="M0 0 Q300 42 601 14 L601 19 Q300 48 0 12 Z" fill="url(#swooshFade)"/>
        <path class="band" d="M0 10 Q300 48 601 18 L601 110 L0 110 Z" fill="var(--brand-navy)"/>
      </svg>
      <address class="footer-contact" style="font-style:normal">
        <div>815 East Darrow Avenue, Suite 4B Chicago, Illinois 60417</div>
        <div>Office: 312-555-0148<span class="sep">|</span>Facsimile: 312-555-0192<span class="sep">|</span>Email: info@maplecrestholdingsllc.example</div>
      </address>
    </footer>
  </main>
</body>
</html>
```